brightwell - Property Management DL Card

I am after a savvy designer to cut through junk mail! so many real estate agents use flyers to promote themselves and their business and usually sales. We are a property management firm (residential) and we want to represent landlords that have existing investment properties and need a quality agent to represent them. Can you help?
DL size, will be printed and delivered to mailboxes. For a look at our website go to www.brightwellrs.com.au. Keep it simple and clutter free.
it is to be double sided - with one side to be simple and clear - just our website, logo and telephone number on the back.
attached is our logo and our telephone number is 1300 48 92 16
the above are 2 essential elements to be included + our email address: admin@brightwellrs.com.au
also attached are our transparent price list

Target Market(s)
property investors,
people that manage properties themselves
Industry/Entity Type
Property Management
- arial
Look and feel

```html
<!DOCTYPE html>
<html lang="en">
<head>
<meta charset="utf-8">
<title>brightwell – Property Management DL Card</title>
<link rel="stylesheet" href="https://fonts.googleapis.com/css2?family=Open+Sans:wght@300;400;600&display=swap">
<style>
  :root {
    --backdrop: #d3d5d5;
    --card-front-frame: #bdb6a8;
    --card-back: #b2aa99;
    --panel-white: #ffffff;
    --ink: #222222;
    --ink-soft: #4a4a4a;
    --bullet: #9a9a9a;
    --band-dark: #141414;
    --heading-text: #e8e4dc;
    --photo-light: #d9cdb5;
    --photo-mid: #8a6a4c;
    --photo-dark: #4a2e1c;
    --rule: #5a5548;
  }
  * { margin: 0; padding: 0; box-sizing: border-box; }
  html, body {
    width: 1200px; height: 1200px; overflow: hidden;
    background: var(--backdrop);
    font-family: "Open Sans", Arial, sans-serif;
  }
  .canvas { position: relative; width: 1200px; height: 1200px; }

  /* Front side */
  .card-front {
    position: absolute; left: 120px; top: 56px; width: 1000px; height: 500px;
    background: var(--card-front-frame);
  }
  .front-photo {
    position: absolute; left: 0; top: 0; width: 668px; height: 500px;
    background:
      linear-gradient(180deg, var(--photo-dark) 0%, var(--photo-mid) 30%, #b89f80 55%, var(--photo-light) 78%, #e2d8c4 100%);
  }
  .front-photo-veil {
    position: absolute; left: 0; width: 668px; height: 23px;
    background: rgba(200, 195, 185, 0.45);
  }
  .front-photo-veil.top { top: 0; }
  .front-photo-veil.bottom { bottom: 0; }
  .front-panel {
    position: absolute; left: 668px; top: 23px; width: 309px; height: 454px;
    background: var(--panel-white);
  }
  .heading-band {
    position: absolute; left: 500px; top: 116px; width: 462px; height: 28px;
    background: linear-gradient(90deg, rgba(20,20,20,0) 0%, rgba(20,20,20,0.85) 7%, var(--band-dark) 75%, rgba(20,20,20,0) 100%);
  }
  .heading-band h1 {
    position: absolute; left: 33px; top: 1px;
    font-size: 18px; font-weight: 600; color: var(--heading-text);
    letter-spacing: 0.2px; white-space: nowrap;
  }
  .benefits {
    position: absolute; left: 697px; top: 155px; list-style: none;
    font-size: 16.5px; color: var(--ink); line-height: 21.5px;
  }
  .benefits li { position: relative; padding-left: 16px; }
  .benefits li::before {
    content: ""; position: absolute; left: 2px; top: 7px;
    width: 7px; height: 7px; background: var(--bullet); transform: rotate(45deg);
  }
  .front-brand {
    position: absolute; left: 750px; top: 386px;
    font-size: 38px; font-weight: 300; color: var(--ink); letter-spacing: -0.5px;
  }

  /* Back side */
  .card-back {
    position: absolute; left: 119px; top: 637px; width: 1002px; height: 501px;
    background: var(--card-back);
  }
  .back-brand-band {
    position: absolute; left: 31px; top: 51px; width: 370px; height: 70px;
    background: linear-gradient(90deg, rgba(20,20,20,0) 0%, rgba(20,20,20,0.9) 14%, var(--band-dark) 30%, var(--band-dark) 70%, rgba(20,20,20,0.9) 86%, rgba(20,20,20,0) 100%);
  }
  .back-brand {
    position: absolute; left: 0; width: 370px; top: 10px; text-align: center;
    font-size: 34px; font-weight: 300; color: #f2f2f2; letter-spacing: -0.5px;
  }
  .contact {
    position: absolute; left: 555px; top: 380px;
    border-left: 2px solid var(--rule); padding-left: 19px;
    font-size: 18px; line-height: 24px; color: var(--ink); letter-spacing: 0.3px;
  }
  .contact .phone { color: var(--ink-soft); }
</style>
</head>
<body>
<main class="canvas">

  <section class="card-front" aria-label="Card front">
    <div class="front-photo" role="img" aria-label="Photograph of a luxury kitchen with timber beamed ceiling, chandeliers, dark wood cabinetry, a cream island bench and stone tile floor"></div>
    <div class="front-photo-veil top"></div>
    <div class="front-photo-veil bottom"></div>
    <div class="front-panel"></div>
    <div class="heading-band"><h1>Property Management specialists</h1></div>
    <ul class="benefits">
      <li>Excellent communication</li>
      <li>No hidden extras</li>
      <li>Minimal vacancy</li>
      <li>The best rent return</li>
    </ul>
    <div class="front-brand">brightwell</div>
  </section>

  <section class="card-back" aria-label="Card back">
    <div class="back-brand-band"><div class="back-brand">brightwell</div></div>
    <address class="contact" style="font-style: normal;">
      <div class="phone">1300 48 92 16</div>
      <div>PO Box C305, Harbourside NSW, 2199</div>
      <div>admin@brightwellrs.com.au</div>
    </address>
  </section>

</main>
</body>
</html>
```